Advertising company unique advertising platform

we need a logo design for a new company based in Australia Melbourne. We develop innovated advertising platform where consumer can use this platform to get regular discount, as business owner they can use this platform for free advertisement. Payment for this advertisement platform only payable every two weeks, when I generate revenue for their business

Industry/Entity Type

Advertising

Contact Information for Business Card

Dale Morven | Co-Founder |Managing Director
Suite 718 240 Wattlebrook Lane Melbourne Vic 3000

ABN 38 614 207 923
Tel: +61 0487 259 318 | Email: dale.morven@plivorantu.com

Font styles to use
Decorative
Script

Requirements
Must have
• Try few different design and some round corner business card
Should not have
• One round corner business card...try 4 different colour background not only black, make sure two side is designed. Be creative so imagine you are giving this to a client make sure has wow factor, if you can also try one design with engrave like all the logo, words look 3d feel
• The word Advertising Platform use attached file font

```html
<!DOCTYPE html>
<html lang="en">
<head>
<meta charset="utf-8">
<title>Plivoran Hub — Business Card</title>
<link href="https://fonts.googleapis.com/css2?family=Marcellus&family=Work+Sans:wght@400;500&display=swap" rel="stylesheet">
<style>
  :root {
    --bg: #e4e4e2;
    --card-dark: #2b2b2b;
    --card-light: #ffffff;
    --ink: #1f1f1f;
    --orange: #f0782a;
    --red: #e5432a;
    --yellow: #f7b733;
    --rule: #3a3a3a;
  }
  * { margin: 0; padding: 0; box-sizing: border-box; }
  html, body { width: 1200px; height: 859px; overflow: hidden; }
  body {
    background: var(--bg);
    font-family: "Work Sans", Arial, sans-serif;
    color: var(--ink);
    position: relative;
  }
  .card {
    position: absolute;
    top: 281px;
    width: 520px;
    height: 297px;
    border-radius: 22px;
    overflow: hidden;
    box-shadow: 0 10px 28px rgba(0,0,0,0.18);
  }
  .card--front { left: 50px; background: var(--card-dark); }
  .card--back { left: 630px; background: var(--card-light); }

  .brand { display: flex; align-items: center; gap: 12px; }
  .brand__dot {
    width: 44px; height: 44px; border-radius: 50%;
    background: var(--orange);
  }
  .brand__name {
    font-family: "Work Sans", Arial, sans-serif;
    font-weight: 500;
    color: var(--orange);
    font-size: 30px;
    letter-spacing: 0.5px;
  }
  .card--front .brand {
    position: absolute; left: 50%; top: 50%;
    transform: translate(-50%, -50%);
  }
  .card--back .brand { position: absolute; left: 28px; top: 28px; }
  .card--back .brand__dot { width: 34px; height: 34px; }
  .card--back .brand__name { font-size: 22px; }

  .person { position: absolute; right: 30px; top: 72px; text-align: right; }
  .person__name {
    font-family: "Marcellus", Georgia, serif;
    color: var(--orange);
    font-size: 25px;
    letter-spacing: 1px;
    line-height: 1;
  }
  .person__role {
    font-family: "Marcellus", Georgia, serif;
    font-size: 10px;
    letter-spacing: 0.4px;
    margin-top: 6px;
  }

  .address {
    position: absolute; left: 30px; top: 108px;
    font-size: 11.5px; line-height: 1.4; letter-spacing: 0.3px;
  }
  .rule {
    position: absolute; left: 30px; right: 30px; top: 150px;
    height: 1px; background: var(--rule);
  }
  .contact { position: absolute; left: 30px; top: 162px; list-style: none; }
  .contact__item {
    display: flex; align-items: center; gap: 9px;
    font-size: 11.5px; letter-spacing: 0.3px; line-height: 1.7;
  }
  .contact__icon { width: 10px; height: 10px; flex: none; }

  .wave { position: absolute; left: 0; bottom: 0; width: 520px; height: 297px; }
  .abn {
    position: absolute; right: 34px; bottom: 44px;
    color: #fff; font-size: 11.5px; letter-spacing: 0.4px;
  }
</style>
</head>
<body>
  <section class="card card--front" aria-label="Card front">
    <div class="brand">
      <span class="brand__dot"></span>
      <span class="brand__name">Plivoran Hub</span>
    </div>
  </section>

  <section class="card card--back" aria-label="Card back">
    <svg class="wave" viewBox="0 0 520 297" aria-hidden="true">
      <defs>
        <linearGradient id="stripe" x1="0" y1="0" x2="1" y2="0">
          <stop offset="0" stop-color="#e5432a"/>
          <stop offset="0.55" stop-color="#f7b733"/>
          <stop offset="0.8" stop-color="#f0782a"/>
          <stop offset="1" stop-color="#e5432a"/>
        </linearGradient>
      </defs>
      <path d="M0 250 C150 256 260 244 340 212 S470 158 520 156 L520 297 L0 297 Z" fill="url(#stripe)"/>
      <path d="M0 258 C150 262 260 252 340 222 S470 168 520 166 L520 297 L0 297 Z" fill="#fff"/>
      <path d="M0 262 C150 266 260 256 340 226 S470 172 520 170 L520 297 L0 297 Z" fill="#2b2b2b"/>
    </svg>

    <div class="brand">
      <span class="brand__dot"></span>
      <span class="brand__name">Plivoran Hub</span>
    </div>

    <div class="person">
      <p class="person__name">DALE MORVEN</p>
      <p class="person__role">|CO-FOUNDER | MANAGING DIRECTOR</p>
    </div>

    <p class="address">Suite 718 240 Wattlebrook<br>Lane Melbourne Vic 3000</p>
    <div class="rule"></div>

    <ul class="contact">
      <li class="contact__item">
        <svg class="contact__icon" viewBox="0 0 10 10" aria-hidden="true"><path d="M2 0.5 L3.6 2.8 L2.6 3.8 C3.2 5.2 4.8 6.8 6.2 7.4 L7.2 6.4 L9.5 8 L8.4 9.5 C4.5 9.3 0.7 5.5 0.5 1.6 Z" fill="#f0782a"/></svg>
        <span>+61 0487 259 318</span>
      </li>
      <li class="contact__item">
        <svg class="contact__icon" viewBox="0 0 10 10" aria-hidden="true"><rect x="0.6" y="2" width="8.8" height="6" fill="none" stroke="#f0782a" stroke-width="1"/><path d="M0.6 2 L5 5.6 L9.4 2" fill="none" stroke="#f0782a" stroke-width="1"/></svg>
        <span>dale.morven@plivorantu.com</span>
      </li>
    </ul>

    <p class="abn">ABN: 38 614 207 923</p>
  </section>
</body>
</html>
```